Preisliste für Kosmetikinstitut
Zielgruppe
Ich benötige für mein Kosmetikinstitut eine Preisliste für die moderne Frau, aber auch Männer. Das Design sollte mein Logo enthalten. Farben des Designkonzepts einbauen.
A4 quer zum Falten, wie ein Heft, 1. Seite Preisliste mit logo, im Innenteil dann Anwendungen
Aufgabenstellung
Minimalistisch, ästhetisch, modern, edel
Kontaktdaten auf der Rückseite
LB Hautatelier
Lotte Brenner
Lindenhang 17
83671 Waakirchen
EMail: lotte@lb-hautatelier.de
Whatsapp: 0176 284 9017

```html
<!DOCTYPE html>
<html lang="de">
<head>
<meta charset="utf-8">
<title>Preisliste – Apparative Behandlungen</title>
<link rel="stylesheet" href="https://fonts.googleapis.com/css2?family=Figtree:wght@300;400;600;700&display=swap">
<style>
  :root{
    --paper-grey:#efeeec;
    --paper-white:#ffffff;
    --ink:#5f6d69;
    --ink-soft:#6b7875;
    --photo-bg:#d6d6d6;
    --photo-skin:#c9a58e;
    --fabric:#eeeeee;
  }
  *{margin:0;padding:0;box-sizing:border-box}
  html,body{width:1200px;height:848px;overflow:hidden}
  body{font-family:"Figtree",sans-serif;color:var(--ink);background:var(--paper-grey);position:relative;font-weight:300}
  .page-left{position:absolute;left:0;top:0;width:669px;height:848px;background:var(--paper-grey)}
  .page-right{position:absolute;left:669px;top:0;width:462px;height:848px;background:var(--paper-white)}
  .block{position:absolute}
  .section-title{font-weight:600;font-size:15.5px;letter-spacing:1.2px;text-transform:uppercase}
  .rule{width:49px;height:1px;background:var(--ink);margin-top:9px}
  .item-title{font-weight:700;font-size:13px;letter-spacing:.9px;line-height:19.5px;text-transform:uppercase}
  .row{display:flex;justify-content:space-between;align-items:baseline}
  .price{font-size:14px;font-weight:400}
  p,li{font-size:12.3px;line-height:17.1px}
  p + p{margin-top:7px}
  .justify{text-align:justify}
  .steps{list-style:none;margin-top:10px}
  .steps li{display:flex;margin-bottom:4.2px}
  .steps .num{width:26px;flex:none;font-size:13px}
  .price-list{margin-top:7px}
  .price-list .row{font-size:12.3px;text-transform:uppercase;letter-spacing:.4px;height:18.5px}
  .price-list .price{letter-spacing:0}
  .extras .row{font-size:14px;font-weight:400;height:18.5px;letter-spacing:.2px}
  .extras .amount{display:flex;width:62px;justify-content:space-between}
  .note{font-size:11px;line-height:14.5px;margin-top:8px}
  .photo-portrait{position:absolute;left:559px;top:100px;width:153px;height:252px;background:linear-gradient(90deg,var(--photo-bg) 55%,var(--photo-skin) 85%,#3a2d28 100%)}
  .photo-fabric{position:absolute;left:487px;top:305px;width:154px;height:94px;border:2px solid #fff;background:radial-gradient(ellipse at 40% 40%,#fafafa,var(--fabric) 60%,#dcdcdc)}
</style>
</head>
<body>
  <div class="page-left"></div>
  <div class="page-right"></div>

  <div class="photo-portrait" role="img" aria-label="Profilfoto einer Frau mit Creme auf der Wange"></div>
  <div class="photo-fabric" role="img" aria-label="Weißer, fließender Seidenstoff"></div>

  <section class="block" style="left:115px;top:77px;width:368px">
    <h1 class="section-title">Apparative Behandlungen</h1>
    <div class="rule"></div>
    <div class="row" style="margin-top:14px;align-items:flex-end">
      <h2 class="item-title">Hydrelia –<br>„Glowing Skin“ Treatment</h2>
      <span class="price">€ 59,00</span>
    </div>
    <p style="margin-top:14px">In 6 Schritten zu einer Haut mit einmaligem Glow- Effekt:</p>
    <ol class="steps">
      <li><span class="num">1.</span><span>Behandlungsschritt: die Haut wird tiefengereinigt</span></li>
      <li><span class="num">2.</span><span>Behandlungsschritt: die obersten Verhornungen und Schuppen werden sanft mit einem Peeling gelöst</span></li>
      <li><span class="num">3.</span><span>Behandlungsschritt: die Haut wird in der Tiefe gereinigt und entschlackt</span></li>
      <li><span class="num">4.</span><span>Behandlungsschritt: niedermolekulare Wirkstoffe werden aufgebracht, um die Haut zu erfrischen und den entsprechenden Glow zu geben</span></li>
      <li><span class="num">5.</span><span>Ausgewählte und hochdosierte Wirkstoffessenzen werden auf dieHaut gesprüht und durch die niedrige Molekularstruktur können diese tiefer in der Haut wirken.</span></li>
      <li><span class="num">6.</span><span>Zum Schluss werden die Essenzen durch eine Impuls-gebende Druckluft- massage noch tiefer in die Haut gebracht; 60min</span></li>
    </ol>
  </section>

  <section class="block" style="left:115px;top:492px;width:370px">
    <h2 class="item-title">Mikrodermabrasion</h2>
    <div class="justify" style="margin-top:13px">
      <p>Bei der Mikrodermabrasion handelt es sich um ein mechanisches Hautpeeling, dabei werden mittels feinster Kristalle die Hornzellen der obersten Hautschicht schonend abgetragen und dann mit Hilfe eines Unterdrucks behutsam abgesaugt.</p>
      <p>Der revitalisierende Prozess erhöht die Durchblutung, fördert die Zellerneuerung und verleiht ihrer Haut ein zartes frisches Gefühl. Die Haut gewinnt an Spannkraft, feine Fältchen werden gemildert und Poren sichtbar verkleinert.</p>
      <p>Außerdem hilft es bei oberflächlichen Akne Narben, Pigment-störungen und Dehnungsstreifen. Wirkstoffe können nun wieder besser von der Haut aufgenommen werden.</p>
    </div>
    <div class="price-list" style="margin-top:9px">
      <div class="row" style="height:20px"><span>Gesicht</span><span class="price">€ 89,00</span></div>
      <div class="row" style="height:20px"><span>Gesicht, Hals, Dekolleté</span><span class="price">€ 110,00</span></div>
    </div>
  </section>

  <section class="block" style="left:739px;top:130px;width:321px">
    <h2 class="section-title" style="font-size:14.5px">Microneedling</h2>
    <div class="justify" style="margin-top:12px">
      <p>Die Behandlung eignet sich besonders für Menschen, die ihre Hautqualität verbessern und Falten, (Akne)Narben, Pigmentverschiebungen, große Poren und sogar Haar-ausfall behandeln wollen.</p>
      <p>Mit Hilfe feinster Nadeln werden der Haut kontrolliert Mikroverletzungen zugeführt, dies regt die natürliche Wundheilung, sowie Kollagen- und Elastin Bildung an. Microneedling ist also eine natürliche Beauty-Behandlung, die körpereigene Reparaturmechanismen nutzt, um ein strafferes Hautbild zu erhalten.</p>
      <p>Bereits nach der ersten Behandlung sieht die Haut aufgepolstert, frisch und rosig aus. Kleine Linien und Fältchen werden tiefenbehandelt. Die Haut wirkt straffer und jugendlicher.</p>
      <p>Ein weiterer Vorteil, durch die Stichkanäle können Wirkstoffe besser von der Haut aufgenommen werden.</p>
    </div>
    <div class="price-list" style="width:312px">
      <div class="row"><span>Gesicht</span><span class="price">€ 110,00</span></div>
      <div class="row"><span>Gesicht, Hals</span><span class="price">€ 130,00</span></div>
      <div class="row"><span>Gesicht, Hals, Dekolleté</span><span class="price">€ 150,00</span></div>
    </div>
  </section>

  <section class="block extras" style="left:739px;top:551px;width:321px">
    <h2 class="section-title" style="font-size:16.5px;font-weight:700">Zusatzleistungen</h2>
    <div class="rule"></div>
    <div style="margin-top:11px;width:321px">
      <div class="row"><span>Augenbrauen zupfen</span><span class="amount"><span>€</span><span>08,00</span></span></div>
      <div class="row"><span>Augenbrauen färben</span><span class="amount"><span>€</span><span>12,00</span></span></div>
      <div class="row"><span>Wimpern färben</span><span class="amount"><span>€</span><span>15,00</span></span></div>
      <div class="row"><span>Enthaarung</span><span class="amount"><span>€</span><span>10,00-</span></span></div>
      <div class="row"><span></span><span class="amount"><span>€</span><span>30,00&nbsp;</span></span></div>
    </div>
    <p class="note" style="margin-top:2px">(Enthaarung der störenden Gesichts-<br>behaarung mittels Wax.)</p>
  </section>
</body>
</html>
```